Business card design needed

We require business cards for our young and innovative construction team.

Our business is Quarry Ridge Builders and we have used Lime, Navy and white with our colours so far.

We would like business cards that show our passion for perfection and detail, communication and management.

Looking forward to seeing the deigns!!

Communication

Dan Ferrante
Quarry Ridge Builders Pty Ltd
PO Box 617 Birchgrove NSW 2041
Mobile: 0471 362 907
Email: dferrante@quarryridgebuilders.com.au
Web: www.quarryridgebuilders.com.au

```html
<!DOCTYPE html>
<html lang="en">
<head>
<meta charset="utf-8">
<title>Quarry Ridge Builders – Business Card</title>
<link href="https://fonts.googleapis.com/css2?family=Open+Sans:wght@400;600;700&display=swap" rel="stylesheet">
<style>
  :root {
    --navy: #2b3a63;
    --navy-deep: #1f2b4d;
    --navy-light: #3a4b7a;
    --lime: #8cc63f;
    --white: #ffffff;
    --ink: #4a4f5c;
    --rule: #c9ccd4;
    --backdrop: #eceae6;
  }
  * { box-sizing: border-box; margin: 0; padding: 0; }
  html, body {
    width: 1200px;
    height: 1024px;
    overflow: hidden;
    background: var(--backdrop);
    font-family: "Open Sans", Arial, sans-serif;
  }
  .sheet {
    width: 1200px;
    height: 1024px;
    display: flex;
    flex-direction: column;
    align-items: center;
    justify-content: center;
    gap: 40px;
  }
  .card {
    width: 800px;
    height: 457px;
    position: relative;
    overflow: hidden;
    box-shadow: 0 6px 18px rgba(0,0,0,0.18);
  }

  /* Front */
  .card-front { background: var(--white); }
  .front-band {
    position: absolute;
    left: 0; right: 0; bottom: 0;
    height: 112px;
    background: var(--navy);
    display: flex;
    align-items: center;
    justify-content: flex-end;
    padding-right: 56px;
  }
  .front-band .web {
    color: var(--white);
    font-size: 17px;
    letter-spacing: 0.3px;
  }
  .front-brand {
    position: absolute;
    top: 70px;
    right: 56px;
    display: flex;
    align-items: center;
    gap: 14px;
  }
  .brand-mark {
    width: 22px;
    height: 22px;
    background: var(--lime);
  }
  .brand-name {
    font-weight: 600;
    color: var(--navy);
    font-size: 32px;
    line-height: 1.1;
  }
  .front-divider {
    position: absolute;
    top: 60px;
    left: 400px;
    width: 2px;
    height: 90px;
    background: var(--rule);
  }
  .contact {
    position: absolute;
    left: 56px;
    top: 178px;
    color: var(--ink);
    font-size: 15px;
    line-height: 1.55;
  }
  .contact .person {
    color: var(--navy);
    font-weight: 700;
    font-size: 26px;
    margin-bottom: 6px;
  }
  .contact .line { display: flex; align-items: center; gap: 8px; }
  .contact svg { width: 14px; height: 14px; flex: none; }

  /* Back */
  .card-back {
    background: radial-gradient(ellipse at 45% 40%, var(--navy-light) 0%, var(--navy) 55%, var(--navy-deep) 100%);
    display: flex;
    flex-direction: column;
    align-items: center;
    justify-content: center;
  }
  .back-brand {
    display: flex;
    align-items: center;
    gap: 18px;
  }
  .back-brand .brand-mark { width: 30px; height: 30px; }
  .back-brand .brand-name {
    color: var(--white);
    font-size: 50px;
  }
  .back-web {
    position: absolute;
    left: 56px;
    bottom: 44px;
    color: var(--white);
    font-size: 17px;
    letter-spacing: 0.3px;
  }
</style>
</head>
<body>
<main class="sheet">
  <section class="card card-front" aria-label="Business card front">
    <div class="front-brand">
      <span class="brand-mark"></span>
      <span class="brand-name">Quarry Ridge Builders</span>
    </div>
    <div class="front-divider"></div>
    <div class="contact">
      <p class="person">Dan Ferrante</p>
      <p>Quarry Ridge Builders Pty Ltd PO Box</p>
      <p>617 Birchgrove NSW 2041</p>
      <p class="line">
        <svg viewBox="0 0 24 24" aria-hidden="true"><path fill="#8cc63f" d="M6.6 10.8a15.1 15.1 0 0 0 6.6 6.6l2.2-2.2c.3-.3.7-.4 1-.2 1.1.4 2.3.6 3.6.6.6 0 1 .4 1 1V20c0 .6-.4 1-1 1A17 17 0 0 1 3 4c0-.6.4-1 1-1h3.5c.6 0 1 .4 1 1 0 1.3.2 2.5.6 3.6.1.3 0 .7-.2 1z"/></svg>
        0471 362 907
      </p>
      <p class="line">
        <svg viewBox="0 0 24 24" aria-hidden="true"><rect x="2" y="5" width="20" height="14" fill="#8cc63f"/><path d="M2 5l10 8 10-8" fill="none" stroke="#fff" stroke-width="2"/></svg>
        dferrante@quarryridgebuilders.com.au
      </p>
    </div>
    <div class="front-band">
      <span class="web">www.quarryridgebuilders.com.au</span>
    </div>
  </section>

  <section class="card card-back" aria-label="Business card back">
    <div class="back-brand">
      <span class="brand-mark"></span>
      <span class="brand-name">Quarry Ridge Builders</span>
    </div>
    <span class="back-web">www.quarryridgebuilders.com.au</span>
  </section>
</main>
</body>
</html>
```